KLO Kelp Lumen Oasis company brochure

We need the design of brochure of a company that provides consultancy, design and supply of key equipment in the field of Wastewater, clean water, organic waste anaerobic treatment and green energy production for Industries. The attached files are:
KLO wording in english that describes activities
Some drawings (useful for design)
Presentation (in italian)
It would be nice to have a 4 pages brochure possibly in double language (english and italian).

Target Market(s)

water and waste

Industry/Entity Type

It Company

Colors

Designer to choose colors to be used in the design.

Requirements
Must have
• use the logo KLO as per attached docs

```html
<!DOCTYPE html>
<html lang="en">
<head>
<meta charset="utf-8">
<title>KLO Kelp Lumen Oasis – Brochure</title>
<link rel="stylesheet" href="https://fonts.googleapis.com/css2?family=Fira+Sans:wght@400;500;600;700&family=Lato:wght@400;700&display=swap">
<style>
  :root{
    --green:#3a9a2a;
    --green-dark:#2f8a22;
    --blue:#1d5fa8;
    --navy:#2b4c8c;
    --ink:#444a52;
    --muted:#8a9099;
    --paper:#ffffff;
    --stage:#e6e7e9;
    --orange:#f08a2c;
  }
  *{box-sizing:border-box;margin:0;padding:0}
  html,body{width:1200px;height:1200px;overflow:hidden;background:var(--stage)}
  body{font-family:"Lato",sans-serif;color:var(--ink);position:relative}
  .spread{position:absolute;left:200px;width:800px;height:563px;background:var(--paper);overflow:hidden;box-shadow:0 4px 14px rgba(0,0,0,.18)}
  .spread--outside{top:30px}
  .spread--inside{top:607px}
  .abs{position:absolute}
  .layer{position:absolute;inset:0;width:800px;height:563px}
  .icon{width:9px;height:9px;flex:none;margin-top:1px}
  .drop{width:7px;height:9px;flex:none;margin-top:1px}

  /* outside */
  .why-title{left:20px;top:10px;font:700 15px "Fira Sans",sans-serif;color:#fff;letter-spacing:.2px}
  .why-list{left:20px;top:62px;width:210px;list-style:none}
  .why-list li{display:flex;gap:7px;font-size:8.4px;line-height:1.36;text-align:justify;margin-bottom:12px}
  .why-list b{font-weight:700;color:#333}
  .treat-title{left:20px;top:238px;font:400 15.5px "Fira Sans",sans-serif;color:var(--navy)}
  .treat-title b{font-weight:700}
  .treat-sub{left:20px;top:258px;font-size:11px;color:#555}
  .treat-list{left:20px;top:284px;list-style:none}
  .treat-list li{display:flex;gap:6px;align-items:center;font-size:11px;color:#555;height:21px}
  .contact{left:45px;top:480px;list-style:none;font-size:7.6px;font-weight:700;color:#333}
  .contact li{display:flex;gap:5px;align-items:center;height:16px}
  .contact svg{width:10px;height:10px}
  .brand{display:flex;align-items:center;gap:6px;font:700 13px/1.05 "Fira Sans",sans-serif;color:var(--green)}
  .brand i{display:block;width:14px;height:14px;background:var(--green)}
  .brand--footer{left:193px;top:496px}
  .brand--cover{left:512px;top:56px;font-size:24px}
  .brand--cover i{width:26px;height:26px}
  .verify{right:22px;top:392px;text-align:right;font-family:"Fira Sans",sans-serif}
  .verify h1{font-size:24px;font-weight:600;color:var(--blue);line-height:1.05}
  .verify .v2{font-size:19.5px;font-weight:600;color:var(--green);line-height:1.15}
  .verify .v3{font-size:16px;font-weight:400;color:var(--blue);line-height:1.3}
  .verify-body{right:22px;top:470px;width:262px;text-align:right;font-size:8px;line-height:1.3;color:#555}
  .verify-body p+p{margin-top:9px}
  .web{left:535px;top:545px;width:245px;display:flex;align-items:center;gap:8px;font-size:7.5px;letter-spacing:3px;color:#333}
  .web::after{content:"";flex:1;height:1px;background:#bbb}

  /* inside */
  .pill{display:inline-block;background:var(--navy);color:#fff;font:700 10px "Fira Sans",sans-serif;padding:1px 8px 2px 4px;border-radius:0 8px 8px 0}
  .pill--green{background:var(--green-dark)}
  .rule{position:absolute;height:1px;background:#b8c4d6}
  .co-list{left:23px;list-style:none}
  .co-list li{display:flex;gap:7px;font-size:7.6px;line-height:1.35;margin-bottom:5px}
  .co-checks{list-style:none}
  .co-checks li{display:flex;gap:5px;align-items:center;font-size:8.2px;height:14px;margin:0}
  .lead{left:23px;top:40px;font-size:8.4px;font-weight:700;color:var(--muted)}
  .str-list{left:23px;top:266px;width:262px;list-style:none}
  .str-list li{display:flex;gap:7px;font-size:7.5px;line-height:1.32;margin-bottom:6px}
  .label-box{left:35px;top:419px;width:114px;height:21px;background:var(--orange);border:1px solid #c96a17;color:#2a2a2a;font-size:7.6px;display:flex;align-items:center;justify-content:center}
  .prov-list{list-style:none;font-size:8.4px;line-height:1.35}
  .prov-list li{position:absolute;display:flex;gap:5px}
  .tech h3{position:absolute;font:600 9.6px "Fira Sans",sans-serif;color:var(--blue)}
</style>
</head>
<body>

<svg width="0" height="0" style="position:absolute" aria-hidden="true">
  <symbol id="i-check" viewBox="0 0 10 10"><rect x="0.6" y="1.6" width="7.6" height="7.6" fill="none" stroke="currentColor" stroke-width="0.9"/><path d="M2.4 5.2 L4.3 7 L9.4 1" fill="none" stroke="currentColor" stroke-width="1.1"/></symbol>
  <symbol id="i-drop" viewBox="0 0 8 10"><path d="M4 0 C5.5 3 7.4 4.6 7.4 6.6 A3.4 3.4 0 0 1 0.6 6.6 C0.6 4.6 2.5 3 4 0Z" fill="#1f8fd6"/></symbol>
  <linearGradient id="g-band" x1="0" y1="0" x2="0" y2="1">
    <stop offset="0" stop-color="#3a9a2a"/><stop offset=".45" stop-color="#2f9340"/><stop offset=".75" stop-color="#1e7a86"/><stop offset="1" stop-color="#1d5fa8"/>
  </linearGradient>
</svg>

<!-- OUTSIDE SPREAD -->
<section class="spread spread--outside">
  <svg class="layer" viewBox="0 0 800 563" aria-hidden="true">
    <defs>
      <linearGradient id="g-fade" x1="0" y1="0" x2="0" y2="1"><stop offset="0" stop-color="#fff"/><stop offset="1" stop-color="#d9dcdf"/></linearGradient>
    </defs>
    <polygon points="0,250 300,250 345,563 0,563" fill="url(#g-fade)" opacity=".55"/>
    <polygon points="228,0 412,0 515,563 334,563" fill="url(#g-band)"/>
    <line x1="420" y1="0" x2="525" y2="563" stroke="#1d5fa8" stroke-width="2"/>
    <polygon points="412,0 420,0 525,563 515,563" fill="#fff"/>
    <polygon points="0,0 228,0 240,38 0,38" fill="var(--green)"/>
  </svg>
  <svg class="layer" viewBox="0 0 800 563" role="img" aria-label="Photo of a large anaerobic digester tank with stairs at a treatment plant under a pale sky">
    <defs>
      <linearGradient id="g-photo" x1="0" y1="0" x2="0" y2="1">
        <stop offset="0" stop-color="#f2f7fb"/><stop offset=".32" stop-color="#dce9f2"/><stop offset=".45" stop-color="#c9a25a"/><stop offset=".8" stop-color="#b48a43"/><stop offset="1" stop-color="#7d8a6a"/>
      </linearGradient>
    </defs>
    <polygon points="424,0 800,0 800,365 493,420" fill="url(#g-photo)"/>
    <line x1="493" y1="420" x2="800" y2="365" stroke="#1d5fa8" stroke-width="2.5"/>
  </svg>

  <div class="abs why-title">WHY TO CHOOSE US ?</div>
  <ul class="abs why-list">
    <li><svg class="drop"><use href="#i-drop"/></svg><span><b>COST REDUCTION :</b> WE first identifies the inefficient processes and remove them.</span></li>
    <li><svg class="drop"><use href="#i-drop"/></svg><span>Only when the emission reduction is not any more possible or economically feasible, WE propose the best treatment to the client.</span></li>
    <li><svg class="drop"><use href="#i-drop"/></svg><span>WE provide best solutions on a variety of biological and chemical processes</span></li>
    <li><svg class="drop"><use href="#i-drop"/></svg><span>WE provide highly qualified and indipended concultancy</span></li>
  </ul>
  <div class="abs treat-title"><b>ANAEROBIC</b> TREATMENT :</div>
  <div class="abs treat-sub">Digestione anaerobica:</div>
  <ul class="abs treat-list" style="color:var(--blue)">
    <li><svg class="icon"><use href="#i-check"/></svg><span>Fanghi</span></li>
    <li><svg class="icon"><use href="#i-check"/></svg><span>Forsu</span></li>
    <li><svg class="icon"><use href="#i-check"/></svg><span>Scarti di macellazione</span></li>
  </ul>
  <ul class="abs contact">
    <li><svg viewBox="0 0 10 10"><path d="M5 1 L9.5 5 H8 V9 H6 V6.5 H4 V9 H2 V5 H0.5Z" fill="var(--navy)"/></svg>Via dei Tigli 58/12 – Torino</li>
    <li><svg viewBox="0 0 10 10"><rect x="1" y="2" width="8" height="6.5" rx="1.2" fill="none" stroke="var(--navy)"/><rect x="3" y="1" width="4" height="2" fill="var(--navy)"/></svg>011.5550192</li>
    <li><svg viewBox="0 0 10 10"><rect x="2.8" y="0.6" width="4.4" height="8.8" rx="0.8" fill="none" stroke="var(--navy)"/><circle cx="5" cy="8" r=".6" fill="var(--navy)"/></svg>333 555 0148</li>
    <li style="padding-left:10px">PIVA: 12345670018</li>
  </ul>
  <div class="abs brand brand--footer"><i></i><span>KLO<br>Kelp Lumen Oasis</span></div>

  <div class="abs brand brand--cover"><i></i><span>KLO<br>Kelp Lumen Oasis</span></div>
  <div class="abs verify">
    <h1>WE VERIFY</h1>
    <div class="v2">any proposed process</div>
    <div class="v3">with its internal labs and &nbsp;pilot tests</div>
  </div>
  <div class="abs verify-body">
    <p>KLO ltd has the mission to solve any client's environmental problem with best process solution available on the market, most reliable and economical both on the CAPEX and OPEX.</p>
    <p>WE want to optimize the client's benefits : energy, water recycle, products recovery and emission minimization.</p>
  </div>
  <div class="abs web">www.kloasis.com</div>
</section>

<!-- INSIDE SPREAD -->
<section class="spread spread--inside">
  <svg class="layer" viewBox="0 0 800 563" aria-hidden="true">
    <polygon points="255,0 429,0 523,555 343,555" fill="url(#g-band)"/>
    <rect x="0" y="555" width="800" height="8" fill="var(--blue)"/>
  </svg>
  <svg class="abs" style="left:33px;top:405px" width="256" height="140" viewBox="0 0 256 140" role="img" aria-label="Line drawing of two anaerobic digester tanks, Digestore 1 and Digestore 2">
    <rect width="256" height="140" fill="#f1f3f6"/>
  </svg>
  <svg class="abs" style="left:518px;top:465px" width="268" height="72" viewBox="0 0 268 72" role="img" aria-label="Line drawing of a treatment plant with buildings and tanks">
    <rect width="268" height="72" fill="#f1f3f6"/>
  </svg>

  <div class="abs" style="left:23px;top:18px"><span class="pill">Our COMPANY :</span></div>
  <div class="rule" style="left:112px;top:25px;width:135px"></div>
  <div class="abs lead">At KLO nasce:</div>
  <ul class="abs co-list" style="top:54px;width:228px">
    <li><svg class="drop"><use href="#i-drop"/></svg><span>from the company Vanti Barili Srl, for over 40 years in the treatment of industrial and liquid waste</span></li>
    <li><svg class="drop"><use href="#i-drop"/></svg><span>from the skills and expertise of their parnters</span></li>
    <li><svg class="drop"><use href="#i-drop"/></svg><span>Esperienza da olte 40 anni nella gestione di processi:</span></li>
  </ul>
  <ul class="abs co-checks" style="left:39px;top:111px;color:var(--navy)">
    <li><svg class="icon"><use href="#i-check"/></svg><span>Biologici aerobici e anaerobici</span></li>
    <li><svg class="icon"><use href="#i-check"/></svg><span>Chimico/fisici</span></li>
    <li><svg class="icon"><use href="#i-check"/></svg><span>Rimozione metalli</span></li>
    <li><svg class="icon"><use href="#i-check"/></svg><span>Riduzione cromati</span></li>
    <li><svg class="icon"><use href="#i-check"/></svg><span>Ossidazione fenton</span></li>
  </ul>
  <ul class="abs co-list" style="top:190px;width:245px">
    <li><svg class="drop"><use href="#i-drop"/></svg><span>I partners hanno progettato, costruito e gestito oltre 250 impianti aerobici e/o anaerobici</span></li>
    <li style="margin-top:4px"><svg class="drop"><use href="#i-drop"/></svg><span>Laboratorio analitico attrezzato e disponibilità di prove pilota</span></li>
  </ul>
  <div class="abs" style="left:23px;top:240px"><span class="pill">Strengths of KLO</span></div>
  <div class="rule" style="left:120px;top:247px;width:140px"></div>
  <ul class="abs str-list" style="color:var(--navy)">
    <li><svg class="icon"><use href="#i-check"/></svg><span style="color:var(--ink)">Attention to the Client with selection of the best available treatment without exception - to optimize efficiency and management and investment costs.</span></li>
    <li><svg class="icon"><use href="#i-check"/></svg><span style="color:var(--ink)">High technological level in its treatment sections, with the possibility of combining them</span></li>
    <li><svg class="icon"><use href="#i-check"/></svg><span style="color:var(--ink)">Provide the client with maximum operating flexibility over a wide range of operating conditions and minimize management costs.</span></li>
    <li><svg class="icon"><use href="#i-check"/></svg><span style="color:var(--ink)">Robustness of the process, thanks to the quality of the materials and the electro-instrumental equipment installed.</span></li>
    <li><svg class="icon"><use href="#i-check"/></svg><span style="color:var(--ink)">Reliability of the technological solution, with installation of backup units where necessary.</span></li>
  </ul>
  <div class="abs label-box">Anaerobic digestion</div>

  <div class="abs" style="left:437px;top:18px"><span class="pill pill--green">WE provide:</span></div>
  <div class="rule" style="left:515px;top:25px;width:262px;background:#c6dcb8"></div>
  <ul class="prov-list" style="color:var(--muted)">
    <li style="left:467px;top:48px"><svg class="icon"><use href="#i-check"/></svg><span style="color:var(--ink)">Feasibility studies</span></li>
    <li style="left:572px;top:48px"><svg class="icon"><use href="#i-check"/></svg><span style="color:var(--ink)">Pilot ttest</span></li>
    <li style="left:470px;top:67px;width:310px"><svg class="icon"><use href="#i-check"/></svg><span style="color:var(--ink);text-align:justify">Process design and guarantees (over 240 plants successfully executed and running)</span></li>
    <li style="left:473px;top:93px"><svg class="icon"><use href="#i-check"/></svg><span style="color:var(--ink)">Basic and detailed engineering</span></li>
    <li style="left:476px;top:109px"><svg class="icon"><use href="#i-check"/></svg><span style="color:var(--ink)">Key equipment support</span></li>
    <li style="left:478px;top:124px"><svg class="icon"><use href="#i-check"/></svg><span style="color:var(--ink)">Construction and start-up supervision</span></li>
    <li style="left:481px;top:139px;width:299px"><svg class="icon"><use href="#i-check"/></svg><span style="color:var(--ink);text-align:justify">Operation and supervision expertise (more than 20 years of internal expertise of various biological and chemical reactions)</span></li>
  </ul>
  <div class="abs" style="left:467px;top:187px"><span class="pill pill--green">Proposed technologies:</span></div>
  <div class="rule" style="left:590px;top:194px;width:187px;background:#c6dcb8"></div>
  <div class="tech">
    <h3 style="left:482px;top:213px">1.&nbsp; Biological processes:</h3>
    <h3 style="left:496px;top:308px">2.&nbsp; High value products recovery</h3>
    <h3 style="left:502px;top:331px">3.&nbsp; Chemico/Phisical processes:</h3>
    <h3 style="left:520px;top:433px">4.&nbsp; Water recovery and recycle</h3>
  </div>
  <ul class="prov-list" style="color:var(--muted)">
    <li style="left:485px;top:232px"><svg class="icon"><use href="#i-check"/></svg><span style="color:var(--ink)">Oxidation, nitrification, denitrification, P-removal</span></li>
    <li style="left:487px;top:247px"><svg class="icon"><use href="#i-check"/></svg><span style="color:var(--ink)">N-recovery and slow release fertilizers production</span></li>
    <li style="left:489px;top:262px"><svg class="icon"><use href="#i-check"/></svg><span style="color:var(--ink)">Anaerobic processes</span></li>
    <li style="left:491px;top:277px"><svg class="icon"><use href="#i-check"/></svg><span style="color:var(--ink)">Metal recovery</span></li>
    <li style="left:506px;top:349px"><svg class="icon"><use href="#i-check"/></svg><span style="color:var(--ink)">Flottation</span></li>
    <li style="left:508px;top:364px"><svg class="icon"><use href="#i-check"/></svg><span style="color:var(--ink)">Filtration and membrane filtration</span></li>
    <li style="left:510px;top:379px;width:270px"><svg class="icon"><use href="#i-check"/></svg><span style="color:var(--ink);text-align:justify">Chemical oxidations / reductions (e.g. Fenton, colour removal, CN, Cr6+ removal ….)</span></li>
    <li style="left:513px;top:405px"><svg class="icon"><use href="#i-check"/></svg><span style="color:var(--ink)">Disinfection</span></li>
  </ul>
</section>

</body>
</html>
```